Single-sided business card for restaurant velmora with new logo made on this site

Business card options with new logo including restaurant name, address, phone number and website. This business card is single-sided only and will be presented at the hostess desk for clients to take. I would like to see options based on a cream card background, a white card background, a yellow card background and a burgundy colored background. It needs to be elegant and traditional.

Target Market(s)

local and international crowd

Industry/Entity Type

restaurant

Contact Information for Business Card

address, website and phone number

Font styles to use
Serif

Colors
EE7325
F08F49
F5BC92
FAE3D3
FDF4ED

Requirements
Must have
• new logo, address, phone number, website
Should not have
• more than three colors

```html
<!DOCTYPE html>
<html lang="es">
<head>
<meta charset="utf-8">
<title>Velmora – Tarjeta de presentación</title>
<link rel="stylesheet" href="https://fonts.googleapis.com/css2?family=Crimson+Text:wght@400;700&display=swap">
<style>
  :root {
    --page-bg: #e4e4e4;
    --card-yellow-top: #f8c146;
    --card-yellow-bottom: #f5b02e;
    --ink-burgundy: #3a181c;
    --band-text: #f5b33a;
  }
  * { margin: 0; padding: 0; box-sizing: border-box; }
  html, body {
    width: 1200px;
    height: 940px;
    overflow: hidden;
    background: var(--page-bg);
  }
  body {
    position: relative;
    font-family: "Crimson Text", Georgia, serif;
    color: var(--ink-burgundy);
  }
  .business-card {
    position: absolute;
    left: 60px;
    top: 162px;
    width: 1080px;
    height: 616px;
    border-radius: 30px;
    overflow: hidden;
    background: linear-gradient(180deg, var(--card-yellow-top), var(--card-yellow-bottom));
  }
  .brand {
    position: absolute;
    left: 0;
    top: 128px;
    width: 100%;
    text-align: center;
  }
  .brand-name {
    font-size: 104px;
    line-height: 1;
    font-weight: 400;
    letter-spacing: 0.01em;
  }
  .brand-since {
    margin-top: 14px;
    font-size: 24px;
    line-height: 1;
    font-weight: 400;
  }
  .address-block {
    position: absolute;
    right: 543px;
    top: 380px;
    text-align: right;
    font-size: 27px;
    line-height: 35px;
    white-space: nowrap;
  }
  .address-block .venue-name { font-weight: 700; }
  .info-divider {
    position: absolute;
    left: 566px;
    top: 391px;
    width: 2px;
    height: 87px;
    background: var(--ink-burgundy);
  }
  .reservations {
    position: absolute;
    left: 583px;
    top: 382px;
    white-space: nowrap;
  }
  .reservations-label {
    font-size: 39px;
    font-weight: 700;
    line-height: 46px;
  }
  .reservations-phone {
    display: flex;
    align-items: center;
    gap: 4px;
    font-size: 50px;
    line-height: 50px;
  }
  .reservations-phone svg { width: 38px; height: 38px; }
  .website-band {
    position: absolute;
    left: 0;
    bottom: 0;
    width: 100%;
    height: 58px;
    background: var(--ink-burgundy);
    color: var(--band-text);
    font-size: 27px;
    font-weight: 700;
    letter-spacing: 0.03em;
    text-align: center;
    line-height: 58px;
  }
</style>
</head>
<body>
  <main class="business-card">
    <header class="brand">
      <div class="brand-name">Velmora</div>
      <div class="brand-since">Desde 1999</div>
    </header>

    <div class="address-block">
      <div class="venue-name">Restaurant Velmora</div>
      <div>Avenida Olmo 417, Bahía Serena</div>
      <div>Oaxaca CP 70312</div>
    </div>

    <div class="info-divider" aria-hidden="true"></div>

    <div class="reservations">
      <div class="reservations-label">Reservaciones</div>
      <div class="reservations-phone">
        <svg viewBox="0 0 24 24" fill="none" stroke="currentColor" stroke-width="1.6" stroke-linecap="round" stroke-linejoin="round" aria-hidden="true">
          <path d="M5 3h3.5l1.8 4.5-2.3 1.4a11 11 0 0 0 6.1 6.1l1.4-2.3 4.5 1.8V18a2 2 0 0 1-2 2A16 16 0 0 1 3 5a2 2 0 0 1 2-2z"/>
          <path d="M14.5 3.5a6 6 0 0 1 6 6"/>
          <path d="M14.5 7a2.5 2.5 0 0 1 2.5 2.5"/>
        </svg>
        <span>958-412-7730</span>
      </div>
    </div>

    <footer class="website-band">www.Velmora.com.mx</footer>
  </main>
</body>
</html>
```